Heron Loan Partners Business Card

We need a business card design for our mortgage servicing company. In addition to servicing the loans of homeowners, we help homeowners with purchasing their homes and any mortgage refinancing. We would like to see designs that use the colors in the logo attached below (gold-ish yellow and navy blue), and any other design you deem fit! The design should communicate a simpler life with smart mortgages provided by Heron.

```html
<!DOCTYPE html>
<html lang="en">
<head>
<meta charset="UTF-8">
<title>Heron Loan Partners Business Card</title>
<link href="https://fonts.googleapis.com/css2?family=Arimo:wght@400;700&display=swap" rel="stylesheet">
<style>
  :root{
    --navy:#221f52;
    --gold:#d4a537;
    --white:#ffffff;
    --ink:#1c1c1c;
    --backdrop:#e4e4e6;
  }
  *{margin:0;padding:0;box-sizing:border-box}
  html,body{width:1200px;height:768px;overflow:hidden;background:var(--backdrop);font-family:"Arimo",sans-serif}
  .canvas{position:relative;width:1200px;height:768px}
  .card{position:absolute;top:230px;width:540px;height:309px;border-radius:22px;overflow:hidden;box-shadow:0 6px 20px rgba(0,0,0,.18)}
  .card-back{left:40px;background:var(--navy)}
  .card-front{left:620px;background:var(--white)}
  .brand{position:absolute;display:flex;align-items:center;gap:10px;font-weight:700;color:var(--gold);white-space:nowrap}
  .brand-dot{border-radius:50%;background:var(--gold);flex:none}
  .card-back .brand{left:50%;top:50%;transform:translate(-50%,-50%);font-size:36px}
  .card-back .brand-dot{width:22px;height:22px}
  .card-front .brand{right:36px;top:52px;font-size:22px;color:var(--navy)}
  .card-front .brand-dot{width:14px;height:14px;background:var(--navy)}
  .holder{position:absolute;left:34px;top:108px}
  .holder-name{font-size:22px;font-weight:700;color:var(--gold);line-height:1}
  .holder-title{font-size:14px;color:var(--navy);margin-top:5px}
  .divider{position:absolute;left:30px;right:40px;top:150px;height:1px;background:var(--ink)}
  .address{position:absolute;left:34px;top:160px;font-size:14px;line-height:19px;color:var(--ink)}
  .contact{position:absolute;right:30px;top:160px;font-size:14px;line-height:20px;color:var(--ink);text-align:right}
  .contact-row{display:flex;justify-content:flex-end;align-items:center;gap:8px}
  .contact-rule{height:1px;background:var(--ink);margin:3px 0 4px 40px}
  .contact svg{width:12px;height:12px;fill:var(--gold)}
  .swoosh{position:absolute;left:0;bottom:0;width:540px;height:120px}
</style>
</head>
<body>
<div class="canvas">
  <section class="card card-back">
    <div class="brand"><span class="brand-dot"></span>Heron Loan Partners</div>
  </section>

  <section class="card card-front">
    <div class="brand"><span class="brand-dot"></span>Heron Loan Partners</div>

    <div class="holder">
      <div class="holder-name">Daniel Carver</div>
      <div class="holder-title">President</div>
    </div>
    <div class="divider"></div>

    <address class="address" style="font-style:normal">
      2716 Harbor Point Lane<br>Bayview, NY 11209
    </address>

    <div class="contact">
      <div class="contact-row">(555) 0142-7789
        <svg viewBox="0 0 24 24"><path d="M6.6 10.8a15 15 0 0 0 6.6 6.6l2.2-2.2a1 1 0 0 1 1-.25 11.4 11.4 0 0 0 3.6.57 1 1 0 0 1 1 1V20a1 1 0 0 1-1 1A17 17 0 0 1 3 4a1 1 0 0 1 1-1h3.5a1 1 0 0 1 1 1c0 1.25.2 2.45.57 3.6a1 1 0 0 1-.25 1z"/></svg>
      </div>
      <div class="contact-rule"></div>
      <div class="contact-row">name@Heron.com
        <svg viewBox="0 0 24 24"><path d="M2 5h20v14H2z M2 5l10 8 10-8" fill="var(--gold)" stroke="#fff" stroke-width="1.5"/></svg>
      </div>
      <div class="contact-row">www.Heron.com
        <svg viewBox="0 0 24 24"><circle cx="12" cy="12" r="10"/></svg>
      </div>
    </div>

    <svg class="swoosh" viewBox="0 0 540 120" preserveAspectRatio="none">
      <path d="M0 40 C120 70 300 120 540 112 L540 120 L0 120 Z" fill="var(--gold)"/>
      <path d="M0 10 C140 30 330 92 540 86 L540 100 C330 104 140 60 0 34 Z" fill="var(--gold)"/>
      <path d="M120 60 C260 80 400 96 540 86 L540 100 C400 104 260 90 120 60 Z" fill="var(--navy)"/>
    </svg>
  </section>
</div>
</body>
</html>
```